Hello my name is Colin, I am Starting a business called Lumen Wellness and fitness and am in need of a memorable business card.
It is a personal training studio. I have added the logo that i would like to be on the left center om my business card. i would like room left up the top for a heading sentence such as. "Is your body shocking for all the wrong reasons". there must be room left on the right of the logo below the main heading for 3 sub headings.
then under those 3 headings and logo room for another larger heading eg. "give me a call and learn how to eat chocolate, drink bear and have great sex". in what room is left i would like to be used for my contact details, use I'm Colin Ferrante your fitness expert on the left then on the right Phone, Email and website space in at least 12 Point. Very specific i know :) now onto the back, for the back i would like an eye catching graphic and room for one main headline and 3 bullet points centered just write anything i will choose what to put in them when i pick a winner. Thank you very much for sticking through all of that :) i appreciate you taking the time to read it and hopefully undergo designing me a business card.
I can't wait to see the designs!

Target Market(s)

slightly more towards females although it would probably be best if it was targeted towards both sexes

Industry/Entity Type

Training

Requirements
Nice to have
• I would love to see if anyone could come up with a design that would really make my card stand out and be memorable.
Should not have
• tacky fitness photos of abs and muscles etc.

```html
<!DOCTYPE html>
<html lang="en">
<head>
<meta charset="utf-8">
<title>Lumen Wellness and Fitness – Business Card</title>
<link rel="stylesheet" href="https://fonts.googleapis.com/css2?family=Questrial&family=Open+Sans:wght@400&display=swap">
<style>
  :root {
    --navy: #1d4a86;
    --navy-deep: #163a6c;
    --navy-light: #2a5ea3;
    --ink: #2b2b2b;
    --grey-text: #4a4a4a;
    --strip: #3a3a3a;
    --card: #ffffff;
    --backdrop: #e6e1da;
    --label: #1a1a1a;
  }
  * { margin: 0; padding: 0; box-sizing: border-box; }
  html, body { width: 1200px; height: 788px; overflow: hidden; }
  body {
    position: relative;
    background: var(--backdrop);
    font-family: "Questrial", "Century Gothic", sans-serif;
    color: var(--ink);
  }
  .view-label {
    position: absolute;
    font-family: "Open Sans", Arial, sans-serif;
    font-size: 20px;
    color: var(--label);
    transform: translateX(-50%);
  }
  .card {
    position: absolute;
    background: var(--card);
    border-radius: 20px;
    overflow: hidden;
    box-shadow: 0 6px 14px rgba(0,0,0,0.25);
  }

  /* Front */
  .card-front { left: 337px; top: 74px; width: 526px; height: 300px; }
  .front-headline {
    position: absolute; left: 0; top: 0; width: 100%; height: 52px;
    background: linear-gradient(180deg, var(--navy-light), var(--navy-deep));
    color: #fff; font-size: 21px; line-height: 52px; padding-left: 32px;
  }
  .brand { position: absolute; color: var(--navy); line-height: 1; }
  .brand-name { display: block; }
  .brand-sub { display: block; }
  .front-brand { left: 35px; top: 92px; }
  .front-brand .brand-name { font-size: 60px; }
  .front-brand .brand-sub { font-size: 16px; margin-top: 4px; padding-left: 52px; }
  .divider {
    position: absolute; left: 271px; top: 91px; width: 1px; height: 107px;
    background: #555;
  }
  .contact { position: absolute; left: 310px; top: 96px; color: var(--navy); font-size: 14px; }
  .contact-name { line-height: 18px; }
  .contact-role { line-height: 18px; }
  .contact-lines { margin-top: 22px; color: var(--grey-text); }
  .contact-line { display: flex; align-items: center; gap: 9px; height: 22px; font-size: 14px; }
  .contact-line svg { width: 12px; height: 12px; fill: var(--grey-text); }
  .front-pitch {
    position: absolute; left: 34px; top: 217px; width: 220px;
    font-size: 13px; line-height: 18px; color: var(--ink);
  }
  .front-strip {
    position: absolute; left: 0; bottom: 0; width: 100%; height: 22px;
    background: var(--strip);
  }
  .front-web-band {
    position: absolute; right: 0; bottom: 0; width: 278px; height: 29px;
    background: linear-gradient(90deg, var(--navy-deep), var(--navy-light));
    clip-path: polygon(14px 0, 100% 0, 100% 100%, 0 100%);
    color: #fff; font-size: 12px; letter-spacing: 2.4px; line-height: 29px;
    padding-left: 58px;
  }

  /* Back 1 */
  .card-back-one { left: 54px; top: 446px; width: 525px; height: 299px; }
  .figure-art {
    position: absolute; left: 41px; top: 20px; width: 146px; height: 262px;
    background: linear-gradient(180deg, var(--navy-light), var(--navy-deep));
    border-radius: 60px 60px 10px 10px;
  }
  .back-one-brand { left: 255px; top: 22px; }
  .back-one-brand .brand-name { font-size: 36px; }
  .back-one-brand .brand-sub { font-size: 9px; margin-top: 2px; padding-left: 30px; }
  .bullets {
    position: absolute; left: 259px; top: 116px; list-style: none;
    font-family: "Open Sans", Arial, sans-serif; font-size: 16px; color: #111;
  }
  .bullets li { position: relative; padding-left: 24px; height: 34px; line-height: 22px; }
  .bullets li:nth-child(2) { height: 36px; }
  .bullets li::before {
    content: ""; position: absolute; left: 0; top: 8px; width: 5px; height: 5px; background: #111;
  }
  .back-one-web {
    position: absolute; left: 256px; top: 253px;
    font-family: "Open Sans", Arial, sans-serif; font-size: 20px; color: var(--grey-text);
  }

  /* Back 2 */
  .card-back-two { left: 621px; top: 441px; width: 524px; height: 299px; }
  .back-two-headline {
    position: absolute; top: 20px; width: 100%; text-align: center;
    font-size: 12px; color: var(--ink);
  }
  .back-two-brand { left: 0; width: 100%; top: 80px; text-align: center; }
  .back-two-brand .brand-name { font-size: 92px; }
  .back-two-brand .brand-sub { font-size: 24px; margin-top: 4px; padding-left: 60px; color: var(--ink); }
  .back-two-web {
    position: absolute; top: 252px; width: 100%; text-align: center;
    font-size: 20px; letter-spacing: 4px; color: var(--grey-text);
  }
</style>
</head>
<body>
  <div class="view-label" style="left:600px; top:32px;">Front</div>
  <div class="view-label" style="left:322px; top:403px;">Back - 1</div>
  <div class="view-label" style="left:897px; top:403px;">Back - 2</div>

  <section class="card card-front">
    <div class="front-headline">Is your body shocking for all the wrong reasons</div>
    <div class="brand front-brand">
      <span class="brand-name">Lumen</span>
      <span class="brand-sub">Wellness and Fitness</span>
    </div>
    <div class="divider"></div>
    <div class="contact">
      <div class="contact-name">Colin Ferrante</div>
      <div class="contact-role">Fitness Expert</div>
      <div class="contact-lines">
        <div class="contact-line">
          <svg viewBox="0 0 12 12" aria-hidden="true"><path d="M2.5 1 L4.5 1 L5.2 3.6 L4 4.6 C4.6 6 5.9 7.3 7.4 8 L8.4 6.8 L11 7.5 L11 9.5 C11 10.3 10.3 11 9.5 11 C5 11 1 7 1 2.5 C1 1.7 1.7 1 2.5 1 Z"/></svg>
          <span>+12 345 67890</span>
        </div>
        <div class="contact-line">
          <svg viewBox="0 0 12 12" aria-hidden="true"><path d="M1 4 L6 1 L11 4 L11 10 L1 10 Z M2 4.6 L6 7 L10 4.6 L6 2.2 Z"/></svg>
          <span>info@website.com</span>
        </div>
      </div>
    </div>
    <p class="front-pitch">give me a call and learn how to eat chocolate, drink bear and have great sex</p>
    <div class="front-strip"></div>
    <div class="front-web-band">www.website.com</div>
  </section>

  <section class="card card-back-one">
    <div class="figure-art" role="img" aria-label="Navy silhouette illustration of a man in a suit and a woman standing side by side"></div>
    <div class="brand back-one-brand">
      <span class="brand-name">Lumen</span>
      <span class="brand-sub">Wellness and Fitness</span>
    </div>
    <ul class="bullets">
      <li>Lorem Ipsum has been ...</li>
      <li>Lorem Ipsum has been ...</li>
      <li>Lorem Ipsum has been ...</li>
    </ul>
    <div class="back-one-web">www.website.com</div>
  </section>

  <section class="card card-back-two">
    <div class="back-two-headline">Is your body shocking for all the wrong reasons</div>
    <div class="brand back-two-brand">
      <span class="brand-name">Lumen</span>
      <span class="brand-sub" style="color:var(--navy);">Wellness and Fitness</span>
    </div>
    <div class="back-two-web">www.website.com</div>
  </section>
</body>
</html>
```